Spring Detox sale graphics for social media

You MUST read the Brief in the WORD document and follow the instructions there. I want to create 10 social media graphics (new Instagram size 4:5 (1080 x 1350 pixels) focusing on our Mother’s Day Spring Detox Sale graphics, using any of the pics attached. Use the attached pics, NO RANDOM STOCK PHOTOGRAPHY. For the color scheme of the graphics, they should all be complementary to the product colors or feel like Spring time.

Target Market(s)

primarily women

Requirements
Must have
• the photos and text attached

```html
<!DOCTYPE html>
<html lang="en">
<head>
<meta charset="utf-8">
<title>Mother's Day Spring Detox Sale</title>
<link rel="stylesheet" href="https://fonts.googleapis.com/css2?family=Anton&family=Oswald:wght@700&family=Kaushan+Script&display=swap">
<style>
  :root {
    --page: #fdf6ea;
    --cream: #f6e4bb;
    --card-fill: #f7e6be;
    --grid-line: rgba(226, 150, 140, .28);
    --frame: #ffffff;
    --pink: #c9669e;
    --plum: #7b4670;
    --bottle: #f1f1f1;
  }
  * { margin: 0; padding: 0; box-sizing: border-box; }
  html, body { width: 960px; height: 1200px; overflow: hidden; background: var(--page); }
  .poster { position: relative; width: 960px; height: 1200px; background: var(--page); }
  .leaf-backdrop {
    position: absolute; left: 18px; top: 18px; width: 924px; height: 1165px;
    background:
      radial-gradient(circle at 8% 30%, rgba(208,127,176,.55), transparent 22%),
      radial-gradient(circle at 94% 20%, rgba(208,127,176,.55), transparent 22%),
      radial-gradient(circle at 6% 75%, rgba(184,90,148,.5), transparent 22%),
      radial-gradient(circle at 95% 70%, rgba(184,90,148,.5), transparent 22%),
      radial-gradient(circle at 30% 3%, rgba(110,50,66,.35), transparent 16%),
      radial-gradient(circle at 70% 98%, rgba(208,127,176,.45), transparent 18%),
      var(--cream);
  }
  .card {
    position: absolute; left: 99px; top: 91px; width: 762px; height: 1018px;
    background: var(--frame); padding: 11px;
    box-shadow: 0 10px 30px rgba(60,30,20,.35);
  }
  .card-inner {
    position: relative; width: 100%; height: 100%;
    background:
      linear-gradient(90deg, var(--grid-line) 1px, transparent 1px) 0 0 / 10px 10px,
      linear-gradient(0deg, var(--grid-line) 1px, transparent 1px) 0 0 / 10px 10px,
      var(--card-fill);
  }
  .headline { position: absolute; left: -110px; top: -102px; width: 960px; height: 1200px; }
  .arc-title { font-family: 'Oswald', sans-serif; font-weight: 700; font-size: 52px; fill: var(--pink); }
  .script-title { font-family: 'Kaushan Script', cursive; font-size: 150px; fill: var(--pink); }
  .banner-text { font-family: 'Oswald', sans-serif; font-weight: 700; font-size: 60px; fill: #fff; letter-spacing: 1px; }
  .offer { font-family: 'Anton', sans-serif; fill: var(--pink); }
  .products {
    position: absolute; left: 74px; top: 674px; width: 597px; height: 254px;
    display: flex; justify-content: space-between; align-items: flex-end;
  }
  .bottle {
    width: 132px; height: 250px; border-radius: 26px 26px 14px 14px;
    background: linear-gradient(180deg, var(--bottle) 0%, #fff 40%, #e4e4e4 100%);
    box-shadow: 0 6px 10px rgba(0,0,0,.18);
  }
  .bottle--liver { background: linear-gradient(180deg, #f2f2f2 0%, #fff 45%, #b96aa6 100%); }
  .bottle--tummy { background: linear-gradient(180deg, #f2f2f2 0%, #fff 45%, #e0403c 100%); height: 240px; }
  .bottle--hormone { background: linear-gradient(180deg, #f2f2f2 0%, #fff 45%, #2f6b55 100%); height: 244px; }
  .bottle--sugar { background: linear-gradient(180deg, #f2f2f2 0%, #fff 45%, #3a4aa8 100%); width: 116px; height: 228px; }
</style>
</head>
<body>
<main class="poster">
  <div class="leaf-backdrop" role="img" aria-label="Illustrated pink and plum spring leaves scattered around the frame"></div>

  <section class="card">
    <div class="card-inner">
      <svg class="headline" viewBox="0 0 960 1200" aria-label="Mother's Day Spring Detox Sale, 25% off everything">
        <defs>
          <path id="title-arc" d="M 392 248 Q 545 135 700 262"/>
        </defs>
        <g class="sparkles" fill="var(--pink)">
          <path d="M304 160 L310 182 L332 188 L310 194 L304 216 L298 194 L276 188 L298 182 Z"/>
          <path d="M336 156 L339 165 L348 168 L339 171 L336 180 L333 171 L324 168 L333 165 Z"/>
          <path d="M330 186 L334 198 L346 202 L334 206 L330 218 L326 206 L314 202 L326 198 Z"/>
        </g>

        <text class="arc-title"><textPath href="#title-arc" startOffset="50%" text-anchor="middle">Mother’s Day</textPath></text>
        <path d="M 440 262 Q 550 200 635 262" fill="none" stroke="var(--pink)" stroke-width="3"/>
        <text class="script-title" x="484" y="318" text-anchor="middle" textLength="410" lengthAdjust="spacingAndGlyphs">Spring</text>

        <polygon class="banner" points="302,337 658,337 645,376 658,415 302,415 315,376" fill="var(--plum)"/>
        <text class="banner-text" x="480" y="398" text-anchor="middle" textLength="258" lengthAdjust="spacingAndGlyphs">DETOX SALE</text>

        <g class="offer-block" transform="rotate(-2 480 580)">
          <text class="offer" x="466" y="576" text-anchor="middle" font-size="122" textLength="420" lengthAdjust="spacingAndGlyphs">25% OFF</text>
          <text class="offer" x="481" y="696" text-anchor="middle" font-size="118" textLength="584" lengthAdjust="spacingAndGlyphs">EVERYTHING!</text>
        </g>
      </svg>

      <div class="products" role="img" aria-label="Photo of four supplement bottles: liver, tummy, hormone and blood sugar formulas">
        <div class="bottle bottle--liver"></div>
        <div class="bottle bottle--tummy"></div>
        <div class="bottle bottle--hormone"></div>
        <div class="bottle bottle--sugar"></div>
      </div>
    </div>
  </section>
</main>
</body>
</html>
```